BildeVOLD buisnesscard

Hey :) I need a modern buisnesscard for my company BildeVOLD
It most have:
Dagligleder og Fotograf: Henrik Audun Strandvik

Mob: +4700012345
Epost: post@bildevold.example
Adresse: Kvernbakken9, 9990 Bildevik

Facbook and instagram logo with text BildeVOLD

BildeVOLD logo

It Company

```html
<!DOCTYPE html>
<html lang="no">
<head>
<meta charset="utf-8">
<title>BildeVOLD – visittkort</title>
<link rel="stylesheet" href="https://fonts.googleapis.com/css2?family=Exo+2:wght@600;700&family=Open+Sans:wght@400&display=swap">
<style>
  :root {
    --stage: #4a4a4a;
    --paper: #ffffff;
    --brand-blue: #2b7db3;
    --blue-light: #4f9fcb;
    --blue-deep: #1f6ea3;
    --brand-pink: #cc4588;
    --pink-stripe: #dd5f98;
    --ink-light: #ffffff;
  }
  * { box-sizing: border-box; margin: 0; padding: 0; }
  html, body { width: 1200px; height: 950px; overflow: hidden; }
  body {
    background: var(--stage);
    font-family: "Open Sans", sans-serif;
    display: flex;
    align-items: center;
    justify-content: center;
    gap: 90px;
  }
  .card {
    position: relative;
    width: 420px;
    height: 680px;
    overflow: hidden;
    box-shadow: 0 12px 30px rgba(0,0,0,.45);
  }
  .card-front { background: var(--paper); }
  .card-back {
    background: var(--brand-pink);
    display: flex;
    align-items: center;
    justify-content: center;
  }
  .card-art { position: absolute; inset: 0; }

  .brand {
    position: absolute;
    top: 118px;
    left: 0; right: 0;
    display: flex;
    align-items: center;
    justify-content: center;
    gap: 12px;
  }
  .brand-mark {
    width: 26px; height: 26px;
    background: var(--brand-pink);
  }
  .brand-name {
    font-family: "Exo 2", sans-serif;
    font-weight: 700;
    font-size: 50px;
    color: var(--brand-blue);
    letter-spacing: .5px;
  }
  .holder {
    position: absolute;
    top: 200px;
    left: 0; right: 0;
    text-align: center;
    font-family: "Exo 2", sans-serif;
    font-weight: 600;
  }
  .holder-name { font-size: 27px; color: var(--brand-blue); letter-spacing: 1px; }
  .holder-role { font-size: 20px; color: var(--brand-pink); margin-top: 4px; letter-spacing: .5px; }

  .contact {
    position: absolute;
    left: 26px;
    bottom: 50px;
    list-style: none;
    color: var(--ink-light);
    font-size: 15px;
    line-height: 27px;
  }
  .contact li { display: flex; align-items: center; gap: 10px; white-space: nowrap; }
  .contact svg { width: 15px; height: 15px; flex: none; }

  .back-name {
    font-family: "Exo 2", sans-serif;
    font-weight: 700;
    font-size: 58px;
    color: var(--ink-light);
    letter-spacing: .5px;
  }
</style>
</head>
<body>

  <section class="card card-front" aria-label="Visittkort, forside">
    <svg class="card-art" viewBox="0 0 420 680" aria-hidden="true">
      <defs>
        <linearGradient id="blueSweep" x1="0" y1="0" x2="1" y2="1">
          <stop offset="0" stop-color="#5aa8d2"/>
          <stop offset="1" stop-color="#1f6ea3"/>
        </linearGradient>
      </defs>
      <polygon points="0,330 140,330 340,680 0,680" fill="url(#blueSweep)"/>
      <polygon points="158,330 176,330 376,680 358,680" fill="var(--pink-stripe)"/>
      <line x1="120" y1="330" x2="320" y2="680" stroke="#ffffff" stroke-width="2"/>
      <line x1="106" y1="330" x2="306" y2="680" stroke="#ffffff" stroke-width="1.5" opacity=".8"/>
      <polygon points="300,610 420,560 420,680 340,680" fill="var(--blue-deep)"/>
      <line x1="290" y1="596" x2="420" y2="542" stroke="var(--blue-light)" stroke-width="2"/>
      <line x1="284" y1="584" x2="420" y2="528" stroke="var(--blue-light)" stroke-width="1.5"/>
    </svg>

    <div class="brand">
      <span class="brand-mark" aria-hidden="true"></span>
      <span class="brand-name">BildeVOLD</span>
    </div>

    <div class="holder">
      <p class="holder-name">Henrik Audun Strandvik</p>
      <p class="holder-role">Dagligleder og Fotograf</p>
    </div>

    <ul class="contact">
      <li>
        <svg viewBox="0 0 16 16" aria-hidden="true"><rect x="4" y="1" width="8" height="14" rx="1.5" fill="none" stroke="#fff" stroke-width="1.5"/><circle cx="8" cy="12.5" r="1" fill="#fff"/></svg>
        +4700012345
      </li>
      <li>
        <svg viewBox="0 0 16 16" aria-hidden="true"><rect x="1" y="3" width="14" height="10" fill="none" stroke="#fff" stroke-width="1.5"/><polyline points="1,3 8,9 15,3" fill="none" stroke="#fff" stroke-width="1.5"/></svg>
        post@bildevold.example
      </li>
      <li>
        <svg viewBox="0 0 16 16" aria-hidden="true"><circle cx="8" cy="8" r="6.5" fill="none" stroke="#fff" stroke-width="1.5"/><line x1="1.5" y1="8" x2="14.5" y2="8" stroke="#fff" stroke-width="1.2"/><ellipse cx="8" cy="8" rx="3" ry="6.5" fill="none" stroke="#fff" stroke-width="1.2"/></svg>
        www.bildevold.example
      </li>
      <li>
        <svg viewBox="0 0 16 16" aria-hidden="true"><path d="M8 15 C4 10 3 8 3 6 a5 5 0 0 1 10 0 c0 2 -1 4 -5 9z" fill="#fff"/><circle cx="8" cy="6" r="1.8" fill="var(--blue-deep)"/></svg>
        Kvernbakken9, 9990 Bildevik
      </li>
    </ul>
  </section>

  <section class="card card-back" aria-label="Visittkort, bakside">
    <span class="back-name">BildeVOLD</span>
  </section>

</body>
</html>
```